Cove medical spa and wellness

Integrate existing logo and web design (colors and background) into tri fold, single card brochure and business card design. We already have a logo and an idea for our promotional material but we would like someone to bring it together for us! Covewellnessandspa.com. We want to see what a marble background with a faded lily (as seen on our webpage) would look like on brochures and business cards.

```html
<!DOCTYPE html>
<html lang="en">
<head>
<meta charset="utf-8">
<title>Cove Medical Spa &amp; Wellness – Menu and Business Card</title>
<link href="https://fonts.googleapis.com/css2?family=EB+Garamond:wght@400;500&family=Pinyon+Script&display=swap" rel="stylesheet">
<style>
:root{
  --stage:#9a9a9a;
  --marble-1:#ffffff;
  --marble-2:#eceded;
  --marble-3:#dcdede;
  --ink:#1e1e1e;
  --gold:#c9a230;
  --gold-light:#e6c64a;
  --gold-soft:#c8a24a;
  --bar:#333333;
  --card-dark:#1c1c1c;
}
*{box-sizing:border-box;margin:0;padding:0}
html,body{width:1200px;height:2995px;overflow:hidden;background:var(--stage)}
body{font-family:"EB Garamond",Georgia,serif;color:var(--ink);font-variant-numeric:oldstyle-nums}
.canvas{position:relative;width:1200px;height:2995px;overflow:hidden;background:var(--stage)}
.abs{position:absolute}

/* shared brand name */
.brand{display:flex;align-items:center;gap:14px;color:var(--gold);font-weight:500;line-height:1.05}
.brand-dot{flex:none;border-radius:50%;background:var(--gold)}
.brand-name{font-family:"EB Garamond",Georgia,serif}

/* flyer */
.flyer{left:55px;top:77px;width:1090px;height:1542px;box-shadow:0 2px 6px rgba(0,0,0,.35);
  background:linear-gradient(160deg,var(--marble-1) 0%,var(--marble-2) 45%,#f6f6f6 70%,var(--marble-3) 100%);overflow:hidden}
.flyer-photo{left:526px;top:0;width:564px;height:667px;
  background:radial-gradient(ellipse at 55% 45%,#ffffff 0%,#f1f1ef 45%,#d9d8d4 75%,#c9c8c4 100%);
  border-bottom-left-radius:60% 40%}
.flyer-stones{left:330px;top:960px;width:420px;height:500px;opacity:.45;
  background:radial-gradient(ellipse at 30% 20%,#dcdcdc 0%,rgba(230,230,230,0) 40%),radial-gradient(ellipse at 70% 60%,#d8d8d8 0%,rgba(230,230,230,0) 35%)}
.flyer .brand{left:71px;top:128px;width:390px}
.flyer .brand-dot{width:44px;height:44px}
.flyer .brand-name{font-size:36px}
.headline{left:71px;top:415px;font-size:57px;line-height:64px;font-weight:400;letter-spacing:.5px}
.headline-rule{left:71px;top:696px;width:358px;height:3px;background:var(--gold)}
.headline-rule::before{content:"";position:absolute;left:0;top:-4px;width:95px;height:11px;background:linear-gradient(90deg,var(--gold),var(--gold-light))}

.section-head{position:absolute;border-top:1px solid #333;border-bottom:1px solid #333;height:33px}
.section-head h2{font-weight:400;font-size:19px;line-height:31px;padding-left:10px;letter-spacing:.2px}
.section-head::after{content:"";position:absolute;left:10px;bottom:-3px;width:90px;height:4px;background:var(--gold)}

.menu-col{position:absolute;font-size:13px;line-height:18px}
.menu-item{position:relative;padding:5px 0 8px}
.menu-item + .menu-item{border-top:2px dotted #666}
.menu-col.right .menu-item:first-child{border-top:2px dotted #666}
.menu-item .price{position:absolute;top:5px}
.menu-col.left .price{left:364px}
.menu-col.right .price{left:352px}
.menu-item .note{color:var(--gold-soft)}
.ticks{list-style:none}
.ticks li{display:flex;align-items:center;gap:4px}
.ticks svg{width:12px;height:12px;flex:none}

.inject-list{position:absolute;left:124px;top:1306px;width:420px;list-style:none;font-size:13px;line-height:16px}
.inject-list li{position:relative;height:31px}
.inject-list .price{position:absolute;left:364px;top:0}

.contact-box{left:593px;top:1206px;width:445px;height:219px;border:2px dashed #444}
.contact-list{list-style:none;position:absolute;left:38px;top:44px}
.contact-list li{display:flex;align-items:center;gap:11px;height:46px;font-size:22px}
.icon{width:29px;height:29px;flex:none}

.address-bar{left:0;top:1467px;width:1090px;height:43px;background:var(--bar);color:#fff;
  font-size:22px;letter-spacing:5.5px;text-align:center;line-height:43px}

/* business card front */
.card-front{left:108px;top:1700px;width:983px;height:562px;box-shadow:0 2px 6px rgba(0,0,0,.35);
  background:linear-gradient(135deg,#f7f7f7 0%,var(--marble-2) 30%,#fafafa 55%,var(--marble-3) 85%,#f2f2f2 100%)}
.card-front .brand{left:55px;top:232px;width:300px}
.card-front .brand-dot{width:38px;height:38px}
.card-front .brand-name{font-size:30px}
.card-divider{left:418px;top:56px;width:1px;height:459px;background:#444}
.card-divider::after{content:"";position:absolute;left:-6px;top:225px;width:13px;height:13px;border-radius:50%;background:#444}
.person-name{left:529px;top:60px;font-family:"Pinyon Script",cursive;font-size:50px;color:var(--gold);line-height:1.1}
.person-role{left:529px;top:130px;font-size:22px}
.card-front .contact-list{left:529px;top:214px}
.card-front .contact-list li{height:56.5px}
.card-address{left:529px;top:447px;font-size:22px;line-height:28px}

/* business card back */
.card-back{left:108px;top:2314px;width:983px;height:562px;box-shadow:0 2px 6px rgba(0,0,0,.35);
  background:linear-gradient(90deg,#2a2a2a 0%,var(--card-dark) 40%,#3a3a3a 70%,#222 100%);overflow:hidden}
.card-back-leaves{left:0;top:50px;width:545px;height:512px;
  background:linear-gradient(150deg,#d6d6d6 0%,#f4f4f4 40%,#e2e2e2 70%,#c9c9c9 100%);
  clip-path:polygon(12% 5%,35% 0,70% 20%,100% 60%,92% 100%,0 100%,0 35%)}
.card-back .brand{left:549px;top:238px;width:380px}
.card-back .brand-dot{width:44px;height:44px}
.card-back .brand-name{font-size:36px}
</style>
</head>
<body>
<div class="canvas">

  <!-- Flyer -->
  <section class="flyer abs" aria-label="IV therapy and injectables menu">
    <div class="flyer-photo abs" role="img" aria-label="White lily, spa stones and a dish of cream on marble"></div>
    <div class="flyer-stones abs" role="img" aria-label="Faded spa stones and lily on marble"></div>

    <div class="brand abs">
      <span class="brand-dot"></span>
      <span class="brand-name">Cove Medical Spa &amp; Wellness</span>
    </div>

    <h1 class="headline abs">PRIORITIZE<br>YOUR<br>HEALTH &amp;<br>WELLNESS</h1>
    <div class="headline-rule abs"></div>

    <div class="section-head" style="left:69px;top:756px;width:441px"><h2>IV THERAPY OPTIONS</h2></div>

    <div class="menu-col left" style="left:69px;top:807px;width:441px">
      <div class="menu-item"><div>Normal Saline</div><div class="note">For rehydration</div><span class="price">$100</span></div>
      <div class="menu-item"><div>Alleviate</div><div class="note">Helps with fatigue, concentration, and insomnia</div>
        <ul class="ticks">
          <li><svg viewBox="0 0 12 12"><circle cx="6" cy="6" r="6" fill="#1e1e1e"/><path d="M3.2 6.2l1.9 1.9 3.7-3.9" stroke="#fff" stroke-width="1.5" fill="none"/></svg>Calcium chloride</li>
          <li><svg viewBox="0 0 12 12"><circle cx="6" cy="6" r="6" fill="#1e1e1e"/><path d="M3.2 6.2l1.9 1.9 3.7-3.9" stroke="#fff" stroke-width="1.5" fill="none"/></svg>Magnesium</li>
          <li><svg viewBox="0 0 12 12"><circle cx="6" cy="6" r="6" fill="#1e1e1e"/><path d="M3.2 6.2l1.9 1.9 3.7-3.9" stroke="#fff" stroke-width="1.5" fill="none"/></svg>Vitamin B12</li>
          <li><svg viewBox="0 0 12 12"><circle cx="6" cy="6" r="6" fill="#1e1e1e"/><path d="M3.2 6.2l1.9 1.9 3.7-3.9" stroke="#fff" stroke-width="1.5" fill="none"/></svg>Blend of Vitamins B1, B2, B3, and B5</li>
        </ul><span class="price">$220</span></div>
      <div class="menu-item"><div>Brainstorm</div>
        <ul class="ticks">
          <li><svg viewBox="0 0 12 12"><circle cx="6" cy="6" r="6" fill="#1e1e1e"/><path d="M3.2 6.2l1.9 1.9 3.7-3.9" stroke="#fff" stroke-width="1.5" fill="none"/></svg>Helps with cognition</li>
          <li><svg viewBox="0 0 12 12"><circle cx="6" cy="6" r="6" fill="#1e1e1e"/><path d="M3.2 6.2l1.9 1.9 3.7-3.9" stroke="#fff" stroke-width="1.5" fill="none"/></svg>Folic acid with B12</li>
          <li><svg viewBox="0 0 12 12"><circle cx="6" cy="6" r="6" fill="#1e1e1e"/><path d="M3.2 6.2l1.9 1.9 3.7-3.9" stroke="#fff" stroke-width="1.5" fill="none"/></svg>L-taurine</li>
          <li><svg viewBox="0 0 12 12"><circle cx="6" cy="6" r="6" fill="#1e1e1e"/><path d="M3.2 6.2l1.9 1.9 3.7-3.9" stroke="#fff" stroke-width="1.5" fill="none"/></svg>Alpha-Lipoic-Acid</li>
        </ul><span class="price">$180</span></div>
    </div>

    <div class="menu-col right" style="left:593px;top:786px;width:439px">
      <div class="menu-item"><div>Get Up and Go</div><div class="note">Helps increase energy levels</div>
        <ul class="ticks">
          <li><svg viewBox="0 0 12 12"><circle cx="6" cy="6" r="6" fill="#1e1e1e"/><path d="M3.2 6.2l1.9 1.9 3.7-3.9" stroke="#fff" stroke-width="1.5" fill="none"/></svg>Amino blend</li>
          <li><svg viewBox="0 0 12 12"><circle cx="6" cy="6" r="6" fill="#1e1e1e"/><path d="M3.2 6.2l1.9 1.9 3.7-3.9" stroke="#fff" stroke-width="1.5" fill="none"/></svg>Blend of Vitamins B1, B2, B3, and B5</li>
        </ul><span class="price">$170</span></div>
      <div class="menu-item"><div>Immunity</div><div class="note">Helps increase immune defense</div>
        <ul class="ticks">
          <li><svg viewBox="0 0 12 12"><circle cx="6" cy="6" r="6" fill="#1e1e1e"/><path d="M3.2 6.2l1.9 1.9 3.7-3.9" stroke="#fff" stroke-width="1.5" fill="none"/></svg>Vitamin C</li>
          <li><svg viewBox="0 0 12 12"><circle cx="6" cy="6" r="6" fill="#1e1e1e"/><path d="M3.2 6.2l1.9 1.9 3.7-3.9" stroke="#fff" stroke-width="1.5" fill="none"/></svg>Blend of Vitamins B1, B2, B3, and B5</li>
          <li><svg viewBox="0 0 12 12"><circle cx="6" cy="6" r="6" fill="#1e1e1e"/><path d="M3.2 6.2l1.9 1.9 3.7-3.9" stroke="#fff" stroke-width="1.5" fill="none"/></svg>Zinc chloride</li>
        </ul><span class="price" style="top:16px">$185</span></div>
      <div class="menu-item"><div>Inner Beauty</div><div class="note">Helps fortify skin, hair and nails</div>
        <ul class="ticks">
          <li><svg viewBox="0 0 12 12"><circle cx="6" cy="6" r="6" fill="#1e1e1e"/><path d="M3.2 6.2l1.9 1.9 3.7-3.9" stroke="#fff" stroke-width="1.5" fill="none"/></svg>Vitamin C</li>
          <li><svg viewBox="0 0 12 12"><circle cx="6" cy="6" r="6" fill="#1e1e1e"/><path d="M3.2 6.2l1.9 1.9 3.7-3.9" stroke="#fff" stroke-width="1.5" fill="none"/></svg>Blend of Vitamins B1, B2, B3, and B5</li>
          <li><svg viewBox="0 0 12 12"><circle cx="6" cy="6" r="6" fill="#1e1e1e"/><path d="M3.2 6.2l1.9 1.9 3.7-3.9" stroke="#fff" stroke-width="1.5" fill="none"/></svg>Biotin</li>
        </ul><span class="price">$195</span></div>
    </div>

    <div class="section-head" style="left:69px;top:1182px;width:441px"><h2>INJECTABLES</h2></div>
    <ul class="inject-list" style="left:69px;top:1229px">
      <li>Vitamin B12 Injection<span class="price">$30</span></li>
      <li>MIC (Methionine, Inisitol, Choline) Injection<span class="price">$30</span></li>
      <li>Amino Blend Injection<span class="price">$30</span></li>
      <li>Vitamin B Complex Injection (Vitamins B1, B2, B3, B5 and B6)<span class="price">$30</span></li>
      <li>Glutathione Injection<span class="price">$30</span></li>
      <li>Tri-Immune Boost Injection<br>To help boost your immune system<br>Mixture of glutathione, Vitamin C and Zinc<span class="price">$40</span></li>
    </ul>

    <div class="contact-box abs">
      <ul class="contact-list">
        <li><svg class="icon" viewBox="0 0 30 30"><circle cx="15" cy="15" r="15" fill="#c9a230"/><path d="M10 8.5c1-.6 1.8-.4 2.3.5l1.2 2.3c.3.7.1 1.3-.5 1.7l-.9.6c.7 1.8 2 3.2 3.8 4l.6-.9c.4-.6 1.1-.8 1.7-.5l2.3 1.2c.9.5 1.1 1.3.5 2.3-1.1 1.7-2.7 2.2-4.6 1.4-3.5-1.5-6-4-7.4-7.5-.8-2 0-3.9 1-5.1z" fill="#fff"/></svg>(602) 555-0142</li>
        <li><svg class="icon" viewBox="0 0 30 30"><circle cx="15" cy="15" r="15" fill="#c9a230"/><rect x="8" y="10" width="14" height="10" fill="none" stroke="#fff" stroke-width="1.4"/><path d="M8 10l7 6 7-6" fill="none" stroke="#fff" stroke-width="1.4"/></svg>welcome@covewellnessandspa.com</li>
        <li><svg class="icon" viewBox="0 0 30 30"><circle cx="15" cy="15" r="15" fill="#c9a230"/><g fill="none" stroke="#fff" stroke-width="1.3"><circle cx="15" cy="15" r="7.5"/><ellipse cx="15" cy="15" rx="3.3" ry="7.5"/><path d="M7.5 15h15M8.6 11h12.8M8.6 19h12.8"/></g></svg>www.covewellnessandspa.com</li>
      </ul>
    </div>

    <div class="address-bar abs">4820 W. HARBOR ROAD, SUITE 12 &nbsp;GLENDALE, AZ 85306</div>
  </section>

  <!-- Business card front -->
  <section class="card-front abs" aria-label="Business card front">
    <div class="brand abs">
      <span class="brand-dot"></span>
      <span class="brand-name">Cove Medical Spa &amp; Wellness</span>
    </div>
    <div class="card-divider abs"></div>
    <div class="person-name abs">Mara Ellison</div>
    <div class="person-role abs">FNP-C, co-owner</div>
    <ul class="contact-list">
      <li><svg class="icon" viewBox="0 0 30 30"><circle cx="15" cy="15" r="15" fill="#c9a230"/><path d="M10 8.5c1-.6 1.8-.4 2.3.5l1.2 2.3c.3.7.1 1.3-.5 1.7l-.9.6c.7 1.8 2 3.2 3.8 4l.6-.9c.4-.6 1.1-.8 1.7-.5l2.3 1.2c.9.5 1.1 1.3.5 2.3-1.1 1.7-2.7 2.2-4.6 1.4-3.5-1.5-6-4-7.4-7.5-.8-2 0-3.9 1-5.1z" fill="#fff"/></svg>(602) 555-0142</li>
      <li><svg class="icon" viewBox="0 0 30 30"><circle cx="15" cy="15" r="15" fill="#c9a230"/><rect x="8" y="10" width="14" height="10" fill="none" stroke="#fff" stroke-width="1.4"/><path d="M8 10l7 6 7-6" fill="none" stroke="#fff" stroke-width="1.4"/></svg>welcome@covewellnessandspa.com</li>
      <li><svg class="icon" viewBox="0 0 30 30"><circle cx="15" cy="15" r="15" fill="#c9a230"/><g fill="none" stroke="#fff" stroke-width="1.3"><circle cx="15" cy="15" r="7.5"/><ellipse cx="15" cy="15" rx="3.3" ry="7.5"/><path d="M7.5 15h15M8.6 11h12.8M8.6 19h12.8"/></g></svg>www.covewellnessandspa.com</li>
    </ul>
    <div class="card-address abs">4820 W. Harbor Road, Suite 12<br>Glendale, AZ 85306</div>
  </section>

  <!-- Business card back -->
  <section class="card-back abs" aria-label="Business card back">
    <div class="card-back-leaves abs" role="img" aria-label="Large white marble-textured lily petals"></div>
    <div class="brand abs">
      <span class="brand-dot"></span>
      <span class="brand-name">Cove Medical Spa &amp; Wellness</span>
    </div>
  </section>

</div>
</body>
</html>
```